Kelvaro.ch is looking for business card letterhead and envelope C5 with WOW effect

We need a strong business card for our company Kelvaro.ch, logo is available. You want a black or dark background on which the logo Stark r% 26 # 252; appears. Letterhead and envelope in C5 format should be in a similar design, but does not have to be We need a strong business card for our company Kelvaro.ch, logo is available. A black or dark background is desired, on which the logo Stark comes across. The letterhead and the envelope in C5 format should have a similar design.

Target Market(s)

Private customers as well as entrepreneurs

Contact Information for Business Card

E-mail: info@kelvaro-example.ch
Web.www.Kelvaro-example.ch
Tel: +41 ( 0 ) 79 482 6037
Adresse:
Lindenweg 14
9406 Tarnbach

Hier kann man Icons verwenden für Email,Tel und Adressse

Font styles to use
Other font styles liked:
• Dubai,bold

Colors

Designer to choose colors to be used in the design.

Requirements
Must have
• WOW effect
Nice to have
• R% 26 # 252; back business card with our service listings. - VEHICLE LABELING - SHOP WINDOW LABELING - STICKERS AND MUCH MORE ... in red color

```html
<!DOCTYPE html>
<html lang="en">
<head>
<meta charset="utf-8">
<title>Kelvaro.ch – Business Card</title>
<link href="https://fonts.googleapis.com/css2?family=Open+Sans:wght@400;600;700;800&display=swap" rel="stylesheet">
<style>
  :root {
    --bg: #4a443e;
    --navy: #18213d;
    --navy-light: #243052;
    --yellow: #fcc419;
    --yellow-soft: #ffd84a;
    --white: #ffffff;
    --red: #e0202a;
  }
  * { box-sizing: border-box; margin: 0; padding: 0; }
  html, body { width: 1200px; height: 930px; overflow: hidden; }
  body {
    background: var(--bg);
    font-family: "Open Sans", sans-serif;
    color: var(--white);
    position: relative;
  }
  .card {
    position: absolute;
    width: 620px;
    height: 400px;
    border-radius: 22px;
    background: linear-gradient(135deg, var(--navy-light) 0%, var(--navy) 55%);
    overflow: hidden;
    box-shadow: 0 14px 30px rgba(0,0,0,.35);
  }
  .card--services { left: 110px; top: 55px; }
  .card--contact { left: 470px; top: 475px; }

  .honeycomb {
    position: absolute;
    border-radius: 10px;
    background: radial-gradient(circle at 40% 40%, var(--yellow-soft), var(--yellow) 70%);
  }
  .card--services .honeycomb { left: 50px; top: 120px; width: 190px; height: 160px; }
  .card--contact .honeycomb { left: 45px; top: 170px; width: 240px; height: 200px; }

  .brand {
    position: absolute;
    font-weight: 800;
    font-size: 44px;
    letter-spacing: 1px;
    color: var(--white);
  }
  .card--services .brand { left: 270px; top: 118px; }
  .card--contact .brand { left: 230px; top: 40px; }

  .services { position: absolute; left: 270px; top: 190px; list-style: none; }
  .services li {
    font-size: 17px;
    text-transform: uppercase;
    line-height: 1.5;
    display: flex;
    align-items: center;
    gap: 10px;
  }
  .services li::after {
    content: "";
    width: 9px; height: 9px;
    border: 2px solid var(--red);
    border-radius: 50%;
  }

  .person { position: absolute; left: 330px; top: 130px; }
  .person__name { font-weight: 800; font-size: 30px; letter-spacing: 1px; }
  .person__name span { color: var(--yellow); }
  .person__role { font-size: 17px; font-weight: 600; margin-top: 2px; }
  .person__rule { width: 46px; height: 2px; background: var(--yellow); margin: 16px 0 14px; }
  .contacts { list-style: none; }
  .contacts li {
    display: flex; align-items: center; gap: 10px;
    font-size: 16px; line-height: 1.75;
  }
  .contacts svg { width: 14px; height: 14px; fill: none; stroke: var(--yellow); stroke-width: 2; flex: none; }
</style>
</head>
<body>
  <section class="card card--services">
    <div class="honeycomb" role="img" aria-label="Yellow honeycomb decoration"></div>
    <div class="brand">KELVARO.CH</div>
    <ul class="services">
      <li>Vehicle labeling</li>
      <li>Shop window labeling</li>
      <li>Stickers and much more</li>
    </ul>
  </section>

  <section class="card card--contact">
    <div class="brand">KELVARO.CH</div>
    <div class="honeycomb" role="img" aria-label="Yellow honeycomb decoration"></div>
    <div class="person">
      <div class="person__name">JONAS <span>BRENNER</span></div>
      <div class="person__role">Director</div>
      <div class="person__rule"></div>
      <ul class="contacts">
        <li><svg viewBox="0 0 24 24"><path d="M5 3h4l2 5-3 2a12 12 0 0 0 6 6l2-3 5 2v4a2 2 0 0 1-2 2A17 17 0 0 1 3 5a2 2 0 0 1 2-2z"/></svg>+41 ( 0 ) 79 482 6037</li>
        <li><svg viewBox="0 0 24 24"><rect x="3" y="5" width="18" height="14" rx="1"/><path d="M3 6l9 7 9-7"/></svg>info@kelvaro-example.ch</li>
        <li><svg viewBox="0 0 24 24"><circle cx="12" cy="12" r="9"/><path d="M3 12h18M12 3c3 3 3 15 0 18M12 3c-3 3-3 15 0 18"/></svg>www.Kelvaro-example.ch</li>
        <li><svg viewBox="0 0 24 24"><path d="M12 22s7-7 7-12a7 7 0 0 0-14 0c0 5 7 12 7 12z"/><circle cx="12" cy="10" r="2.5"/></svg>Lindenweg 14 9406 Tarnbach</li>
      </ul>
    </div>
  </section>
</body>
</html>
```